Modern Business Card

Modern professional business card with more than just logo and demographic info. Something memorable.

We are a trendy/modern chiropractic group with an emphasis on neurology, hence the minimalist-type brain logo. We want to convey that modern and technical aspect with professionalism and the elite nature of our practice environment.

```html
<!DOCTYPE html>
<html lang="en">
<head>
<meta charset="utf-8">
<title>Vertex Chiropractic – Business Card</title>
<link href="https://fonts.googleapis.com/css2?family=Cinzel:wght@500&family=Montserrat:wght@400&display=swap" rel="stylesheet">
<style>
  :root {
    --canvas: #dcdcdc;
    --card-dark: #111111;
    --card-light: #ffffff;
    --brand-blue: #3f7ac4;
    --ink: #1a1a1a;
    --muted: #555555;
    --on-dark: #ffffff;
  }
  * { box-sizing: border-box; margin: 0; padding: 0; }
  html, body { width: 1200px; height: 930px; overflow: hidden; }
  body {
    background: var(--canvas);
    position: relative;
    font-family: "Montserrat", Arial, sans-serif;
  }
  .card {
    position: absolute;
    width: 540px;
    height: 310px;
    border-radius: 22px;
    overflow: hidden;
    box-shadow: 0 6px 14px rgba(0,0,0,0.18);
  }
  .card--back {
    left: 36px; top: 310px;
    background: var(--card-dark);
    display: flex; align-items: center; justify-content: center;
  }
  .card--front { left: 624px; top: 310px; background: var(--card-light); }

  .wordmark {
    font-family: "Cinzel", Georgia, serif;
    font-weight: 500;
    text-align: center;
    line-height: 1;
    letter-spacing: 1px;
  }
  .wordmark__top { display: block; font-size: 44px; }
  .wordmark__bottom { display: block; font-size: 25px; margin-top: 4px; }
  .card--back .wordmark { color: var(--on-dark); }
  .card--front .wordmark {
    position: absolute; right: 34px; top: 40px;
    color: var(--ink);
  }
  .card--front .wordmark__top { font-size: 36px; }
  .card--front .wordmark__bottom { font-size: 20px; }

  .accent-bar {
    position: absolute; left: 0; top: 118px;
    width: 7px; height: 34px; background: var(--brand-blue);
  }
  .person { position: absolute; left: 34px; top: 116px; }
  .person__name {
    font-family: "Cinzel", Georgia, serif;
    font-weight: 500; font-size: 19px;
    color: var(--brand-blue); letter-spacing: 0.5px;
  }
  .person__title { font-size: 12px; color: var(--muted); margin-top: 4px; }

  .address {
    position: absolute; left: 150px; top: 160px;
    font-size: 13px; color: var(--muted); line-height: 1.45;
  }

  .contact-band {
    position: absolute; left: 0; top: 200px;
    width: 440px; height: 86px;
    background: var(--card-dark);
    border-top-right-radius: 14px;
  }
  .contact-list {
    list-style: none;
    position: absolute; left: 150px; top: 12px;
    color: var(--on-dark); font-size: 13px; line-height: 1.55;
  }
  .contact-list li { display: flex; align-items: center; gap: 10px; }
  .contact-list svg { width: 11px; height: 11px; flex: none; }
</style>
</head>
<body>

  <section class="card card--back" aria-label="Card back">
    <h1 class="wordmark">
      <span class="wordmark__top">VERTEX</span>
      <span class="wordmark__bottom">CHIROPRACTIC</span>
    </h1>
  </section>

  <section class="card card--front" aria-label="Card front">
    <h2 class="wordmark">
      <span class="wordmark__top">VERTEX</span>
      <span class="wordmark__bottom">CHIROPRACTIC</span>
    </h2>

    <span class="accent-bar"></span>
    <div class="person">
      <p class="person__name">DANIEL WHITMORE</p>
      <p class="person__title">Director</p>
    </div>

    <p class="address">1187 Cedar Ridge Lane<br>Salem, OR 97301</p>

    <div class="contact-band">
      <ul class="contact-list">
        <li>
          <svg viewBox="0 0 12 12" aria-hidden="true"><path d="M2.5 1h2l1 2.6-1.3.9a6.5 6.5 0 0 0 3.3 3.3l.9-1.3L11 7.5v2A1.5 1.5 0 0 1 9.5 11 8.5 8.5 0 0 1 1 2.5 1.5 1.5 0 0 1 2.5 1z" fill="#fff"/></svg>
          (555) 214-3087
        </li>
        <li>
          <svg viewBox="0 0 12 12" aria-hidden="true"><rect x="1" y="2.5" width="10" height="7" fill="none" stroke="#fff" stroke-width="1"/><path d="M1 2.5l5 4 5-4" fill="none" stroke="#fff" stroke-width="1"/></svg>
          hello@vertexchiro.com
        </li>
        <li>
          <svg viewBox="0 0 12 12" aria-hidden="true"><circle cx="6" cy="6" r="5" fill="none" stroke="#fff" stroke-width="1"/><ellipse cx="6" cy="6" rx="2.2" ry="5" fill="none" stroke="#fff" stroke-width="1"/><path d="M1 6h10" stroke="#fff" stroke-width="1"/></svg>
          www.vertexchiro.com
        </li>
      </ul>
    </div>
  </section>

</body>
</html>
```